Pet store web design

I would like to redesign my current online store (http://furrowlanemart.com)
I'm looking for a clean, modern design. Any ideas are welcome..

Industry/Entity Type

Pet

Number of Pages Required

3 page

```html
<!DOCTYPE html>
<html lang="en">
<head>
<meta charset="utf-8">
<title>Furrow Lane Mart – Pet Store</title>
<link href="https://fonts.googleapis.com/css2?family=Open+Sans:wght@400;600;700;800&display=swap" rel="stylesheet">
<style>
:root{
  --teal:#2bb3b1;
  --teal-dark:#1f9492;
  --yellow:#f5c11d;
  --coral:#e8574b;
  --ink:#333;
  --muted:#888;
  --band:#2f3133;
  --footer:#262728;
  --footer-deep:#1c1d1e;
  --panel:#efefef;
  --white:#fff;
}
*{box-sizing:border-box;margin:0;padding:0}
html,body{width:717px;height:1200px;overflow:hidden}
body{font-family:"Open Sans",Arial,sans-serif;color:var(--ink);background:var(--white);position:relative}
.wrap{width:634px;margin:0 auto}

/* header */
.site-header{height:72px;display:flex;align-items:center;padding:0 18px 0 38px;justify-content:space-between}
.brand{display:flex;align-items:center;gap:6px;font-weight:800;font-size:13px;color:var(--teal);letter-spacing:.2px}
.brand-dot{width:14px;height:14px;border-radius:50%;background:var(--yellow)}
.main-nav{display:flex;gap:18px;font-size:8px;font-weight:700;color:var(--teal);margin-top:14px}
.main-nav span{display:flex;align-items:center;gap:4px}
.main-nav i{width:11px;height:11px;border-radius:50%;background:var(--teal);display:inline-block}
.utility{display:flex;flex-direction:column;align-items:flex-end;gap:6px}
.account-links{display:flex;gap:10px;font-size:6.5px;color:var(--muted)}
.search{width:118px;height:16px;border:1px solid #ddd;display:flex;justify-content:space-between;align-items:center;font-size:6.5px;color:#aaa;padding-left:5px}
.search b{width:16px;height:16px;background:var(--teal);display:flex;align-items:center;justify-content:center}

/* hero */
.hero{position:relative;height:283px;background:linear-gradient(100deg,#2f3032 0%,#4b4c4f 45%,#77787b 70%,#9b3a34 82%,#5a5b5e 100%)}
.hero-copy{position:absolute;left:92px;top:46px;color:var(--white);width:270px}
.hero-copy h1{font-size:34px;font-weight:800;letter-spacing:1px}
.hero-copy p{font-size:12.5px;line-height:1.35;margin:6px 0 14px}
.btn{display:inline-block;font-weight:700;font-size:7px;padding:5px 10px;color:var(--white);background:var(--teal)}
.hero-arrow{position:absolute;top:86px;width:14px;height:28px}
.hero-arrow.left{left:28px}.hero-arrow.right{right:28px}
.features{position:absolute;left:0;right:0;bottom:0;height:57px;background:rgba(40,41,43,.92);display:flex;justify-content:center;gap:0}
.feature{width:150px;display:flex;align-items:center;gap:8px;color:var(--white)}
.feature-icon{width:24px;height:24px;border-radius:50%;background:var(--white);display:flex;align-items:center;justify-content:center}
.feature h3{font-size:8.5px;font-weight:800;color:var(--yellow)}
.feature small{font-size:6.5px;color:#ccc;display:block}

/* promos */
.promos{padding-top:23px;display:grid;grid-template-columns:repeat(3,1fr);gap:8px}
.promo{height:145px;position:relative;overflow:hidden}
.promo-photo{position:absolute;inset:0}
.promo-text{position:absolute;left:0;bottom:0;width:58%;height:64%;background:var(--teal);color:var(--white);padding:10px 10px}
.promo-text.alt{width:60%}
.promo-text strong{display:block;font-size:16px;font-weight:800;line-height:1}
.promo-text span{display:block;font-size:9.5px;font-weight:600;line-height:1.2;margin-top:3px}
.promo-text .big{font-size:30px}
.promo .btn{position:absolute;right:8px;bottom:10px;background:var(--band);font-size:6px;padding:4px 7px}

/* popular */
.popular{background:var(--panel);margin-top:17px;padding:14px 0 20px;height:227px}
.section-head{display:flex;justify-content:space-between;align-items:center;margin-bottom:10px}
.section-head h2{font-size:11px;font-weight:800}
.pager{display:flex;gap:4px}
.pager i{width:10px;height:10px;border-radius:50%;background:#555;display:block}
.products{display:grid;grid-template-columns:repeat(4,1fr);gap:11px}
.product{background:var(--white);height:172px;padding:10px}
.product-photo{height:105px}
.product h4{font-size:6.5px;font-weight:700;text-align:center;margin:10px 0 8px;color:#555}
.product-row{display:flex;justify-content:space-between;align-items:center}
.price{font-size:14px;font-weight:800;color:var(--teal)}
.add{background:var(--yellow);color:var(--ink);font-size:5.5px;font-weight:800;padding:4px 6px}

/* newsletter */
.newsletter{background:var(--coral);height:51px;margin-top:0}
.newsletter .wrap{display:flex;justify-content:space-between;align-items:center;height:100%}
.newsletter h2{color:var(--white);font-size:11px;font-weight:800}
.newsletter p{color:#fbd6d1;font-size:6.5px}
.signup{display:flex}
.signup span{width:178px;height:19px;background:var(--white);font-size:6.5px;color:#999;padding:5px 6px}
.signup b{background:var(--teal);color:var(--white);font-size:8px;font-weight:800;padding:4px 14px}

/* footer */
.site-footer{background:var(--footer);height:180px;padding-top:16px}
.footer-cols{display:grid;grid-template-columns:1.7fr 1fr 1fr 1fr 1.2fr;gap:12px}
.footer-cols h5{font-size:7.5px;font-weight:800;color:var(--yellow);margin-bottom:6px}
.footer-cols h5.brand-col{color:var(--teal)}
.footer-cols p,.footer-cols li{font-size:6px;color:#aaa;line-height:1.6;list-style:none}
.footer-bar{background:var(--footer-deep);height:17px}
.footer-bar .wrap{display:flex;justify-content:space-between;align-items:center;height:100%;font-size:5.5px;color:#888}
.cards{display:flex;gap:3px}
.cards i{width:16px;height:9px;background:#ddd;border-radius:1px;display:block}
</style>
</head>
<body>

<header class="site-header">
  <div class="brand"><span class="brand-dot"></span>Furrow Lane Mart</div>
  <nav class="main-nav">
    <span><i></i>DOG</span><span><i></i>CAT</span><span><i></i>FISH</span><span><i></i>BIRD</span><span><i></i>SMALL PET</span>
  </nav>
  <div class="utility">
    <div class="account-links"><span>Log in</span><span>My Account</span><span>Wishlist</span><span>Checkout</span></div>
    <div class="search">Search...<b><svg width="8" height="8" viewBox="0 0 10 10"><circle cx="4" cy="4" r="3" fill="none" stroke="#fff" stroke-width="1.5"/><line x1="6.2" y1="6.2" x2="9" y2="9" stroke="#fff" stroke-width="1.5"/></svg></b></div>
  </div>
</header>

<section class="hero">
  <div class="promo-photo" role="img" aria-label="Small dog wearing a red winter jacket"></div>
  <svg class="hero-arrow left" viewBox="0 0 14 28"><polyline points="12,2 2,14 12,26" fill="none" stroke="#fff" stroke-width="2"/></svg>
  <svg class="hero-arrow right" viewBox="0 0 14 28"><polyline points="2,2 12,14 2,26" fill="none" stroke="#fff" stroke-width="2"/></svg>
  <div class="hero-copy">
    <h1>WELCOME</h1>
    <p>Shop through a wide variety of pet accessories in the comfort of your home!</p>
    <span class="btn">SHOP NOW</span>
  </div>
  <div class="features">
    <div class="feature"><span class="feature-icon"><svg width="12" height="10" viewBox="0 0 12 10"><rect x="0" y="2" width="7" height="5" fill="#333"/><polygon points="7,4 10,4 12,6 12,7 7,7" fill="#333"/><circle cx="3" cy="8.5" r="1.3" fill="#333"/><circle cx="9.5" cy="8.5" r="1.3" fill="#333"/></svg></span><div><h3>DELIVERY</h3><small>INFORMATION</small></div></div>
    <div class="feature"><span class="feature-icon"><svg width="12" height="12" viewBox="0 0 12 12"><path d="M2 6a4 4 0 1 0 1.2-2.8" fill="none" stroke="#333" stroke-width="1.5"/><polygon points="1,1 4,3.5 1,5" fill="#333"/></svg></span><div><h3>RETURNS</h3><small>POLICY</small></div></div>
    <div class="feature"><span class="feature-icon"><svg width="10" height="12" viewBox="0 0 10 12"><text x="5" y="10" text-anchor="middle" font-size="11" font-weight="800" fill="#333" font-family="Open Sans">?</text></svg></span><div><h3>QUESTIONS</h3><small>VIEW FAQS</small></div></div>
    <div class="feature"><span class="feature-icon"><svg width="12" height="12" viewBox="0 0 12 12"><path d="M3 1l2 3-1.3 1.2a7 7 0 0 0 3 3L8 7l3 2-1 2C5 11 1 7 1 2z" fill="#333"/></svg></span><div><h3>LET US HELP</h3><small>CONTACT US</small></div></div>
  </div>
</section>

<section class="wrap promos">
  <article class="promo"><div class="promo-photo" role="img" aria-label="Assorted colourful dog sweaters" style="background:linear-gradient(135deg,#e7e7e7,#c9d6c2 50%,#d98a8a)"></div><div class="promo-text"><strong class="big">30</strong><span>New Pet Products Every Month</span></div><span class="btn">SHOP NOW</span></article>
  <article class="promo"><div class="promo-photo" role="img" aria-label="Soft rubber dog toys" style="background:linear-gradient(135deg,#f0f0f0,#f2b8c4 50%,#9fd0e6)"></div><div class="promo-text"><strong>TOYS</strong><span>Shop Soft Rubber Toys!</span></div><span class="btn">SHOP NOW</span></article>
  <article class="promo"><div class="promo-photo" role="img" aria-label="Small dog bed" style="background:linear-gradient(135deg,#ececec,#b8a48e 55%,#8a7560)"></div><div class="promo-text"><strong>BEDS</strong><span>Small Dog Pet Beds</span></div><span class="btn">SHOP NOW</span></article>
  <article class="promo"><div class="promo-photo" role="img" aria-label="Dog in a police costume" style="background:linear-gradient(135deg,#e9e9e9,#4d6a9a 55%,#2d3f66)"></div><div class="promo-text alt"><strong>FALL WINTER</strong><span>Show em who's Boss!</span></div><span class="btn">SHOP NOW</span></article>
  <article class="promo"><div class="promo-photo" role="img" aria-label="Dogs in knitted winter sweaters" style="background:linear-gradient(135deg,#ededed,#8fb07a 50%,#c9514a)"></div><div class="promo-text alt"><strong>FALL WINTER</strong><span>Keep Your Pet Warm With Style!</span></div><span class="btn">SHOP NOW</span></article>
  <article class="promo"><div class="promo-photo" role="img" aria-label="Dog in a superhero costume" style="background:linear-gradient(135deg,#eeeeee,#d84b4b 55%,#3f61a8)"></div><div class="promo-text alt"><strong>FALL WINTER</strong><span>Too Fast For Human Eye!</span></div><span class="btn">SHOP NOW</span></article>
</section>

<section class="popular">
  <div class="wrap">
    <div class="section-head"><h2>MOST POPULAR</h2><div class="pager"><i></i><i></i></div></div>
    <div class="products">
      <article class="product"><div class="product-photo" role="img" aria-label="Dog in a chef costume" style="background:linear-gradient(#fff,#e6e6e6 60%,#f3f3f3)"></div><h4>CHEF DOG COSTUME LARGE</h4><div class="product-row"><span class="price">$30.69</span><span class="add">ADD TO CART</span></div></article>
      <article class="product"><div class="product-photo" role="img" aria-label="Round green pet bed" style="background:radial-gradient(ellipse at center,#9fb06a,#6f8040 55%,#fff 72%)"></div><h4>CHEF DOG COSTUME LARGE</h4><div class="product-row"><span class="price">$30.69</span><span class="add">ADD TO CART</span></div></article>
      <article class="product"><div class="product-photo" role="img" aria-label="Dog in a green costume" style="background:radial-gradient(ellipse at center,#9cc63c,#7aa52a 45%,#fff 70%)"></div><h4>CHEF DOG COSTUME LARGE</h4><div class="product-row"><span class="price">$30.69</span><span class="add">ADD TO CART</span></div></article>
      <article class="product"><div class="product-photo" role="img" aria-label="Dog on a grass training mat" style="background:radial-gradient(ellipse at center,#5a8a3a,#3f3f3f 50%,#fff 72%)"></div><h4>CHEF DOG COSTUME LARGE</h4><div class="product-row"><span class="price">$30.69</span><span class="add">ADD TO CART</span></div></article>
    </div>
  </div>
</section>

<section class="newsletter">
  <div class="wrap">
    <div><h2>NEWSLETTER SIGN UP</h2><p>Keep up to date on the latest offers and new products.</p></div>
    <div class="signup"><span>Enter Email Address</span><b>SIGN UP</b></div>
  </div>
</section>

<footer>
  <div class="site-footer">
    <div class="wrap footer-cols">
      <div><h5 class="brand-col">FURROW LANE MART</h5><p>We care about pets and the people who love them. Visit furrowlanemart.com for quality accessories, friendly advice and fast delivery right to your door.</p></div>
      <div><h5>ABOUT US</h5><ul><li>About Us</li><li>Careers</li><li>Pet Blog</li><li>Contact Us</li></ul></div>
      <div><h5>SHOP NOW</h5><ul><li>Dog</li><li>Cat</li><li>Fish</li><li>Bird</li><li>Small Pet</li><li>Small Animals</li></ul></div>
      <div><h5>SERVICES</h5><ul><li>Pet Grooming</li><li>Pet Adoption</li><li>DIY Dog Wash</li><li>Pet Hotel</li><li>Puppy School</li></ul></div>
      <div><h5>SHOPPING ONLINE</h5><ul><li>Delivery Information</li><li>Privacy Policy</li><li>Returns Policy</li><li>Terms and Conditions</li><li>FAQs</li></ul></div>
    </div>
  </div>
  <div class="footer-bar">
    <div class="wrap"><span>© 2024 furrowlanemart.com. All Rights Reserved.</span><div class="cards"><i></i><i></i><i></i></div></div>
  </div>
</footer>

</body>
</html>
```